Communication and Marketing agency needs a new presentation card

We are a group of communication and marketing agencies specialized in companies that are in the logistics and industrial sector. The head agency is TELVANO Grupo and the group consists of 4 agencies: TELVANO Media, TELVANO Digital, TELVANO Research and DifundeEnPantalla. We hace 4 offices in Spain (Madrid, Barcelona, Valencia and Murcia). We are looking for a clean and attractive design that transmits our experience, brand presence in the market and knowledge to those who receive the card.It has to maintain the colors of the logo that is attached.
Target Market(s)
logistics and industrial sector
Marketing department
Contact Information for Business Card
Clean and attractive design

```html
<!DOCTYPE html>
<html lang="en">
<head>
<meta charset="utf-8">
<title>TELVANO Grupo – Business Card</title>
<link rel="stylesheet" href="https://fonts.googleapis.com/css2?family=Open+Sans:wght@300;400;600&family=Tinos:wght@400;700&display=swap">
<style>
  :root {
    --brand-red: #b31e24;
    --slate: #58585a;
    --slate-band: #4a4a4d;
    --white: #ffffff;
    --backdrop: #1e1e1f;
  }
  * { box-sizing: border-box; margin: 0; padding: 0; }
  html, body {
    width: 1200px; height: 900px; overflow: hidden;
    background: var(--backdrop);
    font-family: "Open Sans", Arial, sans-serif;
  }
  .stage { position: relative; width: 1200px; height: 900px; }

  .card {
    position: absolute;
    width: 600px; height: 343px;
    border-radius: 3px;
    overflow: hidden;
  }

  /* Front */
  .card-front { left: 80px; top: 90px; background: var(--brand-red); }
  .card-front .base-band {
    position: absolute; left: 0; right: 0; bottom: 0; height: 40px;
    background: var(--slate-band);
  }
  .brand-block {
    position: absolute; left: 44px; top: 110px; width: 230px;
    color: var(--white);
  }
  .brand-name {
    font-weight: 300; font-size: 34px; letter-spacing: 1px; line-height: 1;
  }
  .brand-name span { font-size: 20px; letter-spacing: 0; }
  .agency-list {
    display: flex; gap: 12px; margin-top: 26px;
    font-weight: 300; font-size: 9px; letter-spacing: .3px;
  }
  .divider {
    position: absolute; left: 300px; top: 52px; width: 2px; height: 200px;
    background: var(--white);
  }
  .contact-block {
    position: absolute; left: 330px; top: 56px; color: var(--white);
  }
  .person-name {
    font-family: "Tinos", "Times New Roman", serif; font-weight: 700; font-size: 24px;
  }
  .person-role {
    font-family: "Tinos", "Times New Roman", serif; font-size: 17px; margin-bottom: 12px;
  }
  .contact-row {
    display: flex; align-items: flex-start; gap: 10px;
    font-size: 13px; line-height: 18px; margin-bottom: 4px;
  }
  .contact-row .icon { flex: 0 0 18px; width: 18px; height: 18px; }
  .phone-lines { display: grid; grid-template-columns: auto auto; column-gap: 6px; }

  /* Back */
  .card-back {
    left: 520px; top: 468px; background: var(--slate);
    display: flex; align-items: center; justify-content: center;
  }
  .back-brand {
    color: var(--brand-red); font-weight: 300; font-size: 64px; letter-spacing: 2px; line-height: 1;
  }
  .back-brand span { font-size: 36px; letter-spacing: 0; }
</style>
</head>
<body>
<main class="stage">
  <section class="card card-front" aria-label="Card front">
    <div class="brand-block">
      <div class="brand-name">TELVANO <span>Grupo</span></div>
      <div class="agency-list">
        <span>TELVANO Research</span>
        <span>TELVANO Digital</span>
        <span>TELVANO Media</span>
      </div>
    </div>
    <div class="divider"></div>
    <div class="contact-block">
      <div class="person-name">Your Name</div>
      <div class="person-role">Position</div>
      <div class="contact-row">
        <svg class="icon" viewBox="0 0 18 18"><circle cx="9" cy="9" r="9" fill="#fff"/><path d="M6 4.5l1.6 0 .8 2.2-1 .8a6 6 0 0 0 3 3l.8-1 2.2.8 0 1.6c0 .6-.5 1-1.1 1A7.5 7.5 0 0 1 5 5.6c0-.6.4-1.1 1-1.1z" fill="var(--brand-red)"/></svg>
        <div class="phone-lines">
          <span>Office</span><span>: +0.000.000.0000</span>
          <span>Cell</span><span>: +0.000.000.0000</span>
        </div>
      </div>
      <div class="contact-row">
        <svg class="icon" viewBox="0 0 18 18"><circle cx="9" cy="9" r="9" fill="#fff"/><rect x="4.5" y="6" width="9" height="6.5" fill="none" stroke="var(--brand-red)" stroke-width="1.2"/><path d="M4.5 6l4.5 3.8L13.5 6" fill="none" stroke="var(--brand-red)" stroke-width="1.2"/></svg>
        <span>info@telvanogrupo.com</span>
      </div>
      <div class="contact-row">
        <svg class="icon" viewBox="0 0 18 18"><circle cx="9" cy="9" r="9" fill="#fff"/><g fill="none" stroke="var(--brand-red)" stroke-width="1.1"><circle cx="9" cy="9" r="4.8"/><ellipse cx="9" cy="9" rx="2" ry="4.8"/><path d="M4.2 9h9.6"/></g></svg>
        <span>www.telvanogrupo.com</span>
      </div>
      <div class="contact-row">
        <svg class="icon" viewBox="0 0 18 18"><circle cx="9" cy="9" r="9" fill="#fff"/><path d="M9 3.8a3.6 3.6 0 0 0-3.6 3.6c0 2.7 3.6 6.8 3.6 6.8s3.6-4.1 3.6-6.8A3.6 3.6 0 0 0 9 3.8z" fill="var(--brand-red)"/><circle cx="9" cy="7.4" r="1.3" fill="#fff"/></svg>
        <span>Office Address</span>
      </div>
    </div>
    <div class="base-band"></div>
  </section>

  <section class="card card-back" aria-label="Card back">
    <div class="back-brand">TELVANO <span>Grupo</span></div>
  </section>
</main>
</body>
</html>
```